Event Center Website

We need a new website design for an upscale event center in Reno, Nevada. The building hosts everything from weddings to corporate events to funerals and it competitively more expensive. The overall look and feel is consistent with a Lake Tahoe aesthetic. The current site can be viewed at www.themaplehallevents.com. They are looking for a major upgrade. A sample site they like is www.cliffsidelodgestay.com. We have new photography available (some attached). The site should be very visual. A site map is attached as well for direction on what elements the site should include as well as labels for navigation. I am looking for a home page and sample interior page. Any questions, let me know. Thanks.
Updates

I have added some photography of the center itself for use rather than stock photography. Thanks!

Target Market(s)

Brides, professionals, high-income

Industry/Entity Type

Building

Requirements
Must have
• See site map

```html
<!DOCTYPE html>
<html lang="en">
<head>
<meta charset="utf-8">
<title>Maple Hall at Pine Ridge</title>
<link href="https://fonts.googleapis.com/css2?family=PT+Sans+Narrow:wght@400;700&family=Open+Sans:wght@400&display=swap" rel="stylesheet">
<style>
  :root{
    --cream:#f6ecd5;
    --brown-dark:#3b2312;
    --brown:#5a3216;
    --footer:#1b0706;
    --footer-text:#b9a58c;
    --panel:rgba(60,60,64,.72);
    --panel-light:rgba(70,70,74,.6);
    --field-border:#9b8465;
  }
  *{box-sizing:border-box;margin:0;padding:0}
  html,body{width:1200px;height:826px;overflow:hidden}
  body{background:var(--cream);font-family:"PT Sans Narrow",sans-serif;position:relative}

  .site-header{position:absolute;left:0;top:0;width:1200px;height:118px;background:var(--cream)}
  .brand{position:absolute;left:98px;top:28px;height:56px;display:flex;align-items:center;gap:10px}
  .brand-square{width:18px;height:18px;background:var(--brown)}
  .brand-name{font-size:30px;font-weight:700;color:var(--brown);letter-spacing:.5px;white-space:nowrap}
  .main-nav{position:absolute;left:336px;top:48px;width:767px;display:flex;justify-content:space-between}
  .main-nav a{font-size:14px;color:var(--brown-dark);text-decoration:none;text-transform:uppercase;white-space:nowrap}

  .hero{position:absolute;left:0;top:118px;width:1200px;height:563px;overflow:hidden}
  .hero-photo{position:absolute;inset:0;
    background:
      radial-gradient(ellipse 55% 35% at 52% 88%, #f6f4f2 0%, #e9e5e1 50%, rgba(233,229,225,0) 100%),
      radial-gradient(ellipse 30% 40% at 60% 20%, #efe0bf 0%, rgba(239,224,191,0) 100%),
      linear-gradient(90deg,#6b2a12 0%,#a95a34 14%,#d9c4a8 30%,#e8dcc4 50%,#d8c6a6 68%,#8e5a3a 82%,#5a3a22 100%);}
  .hero-floor{position:absolute;left:0;right:0;bottom:0;height:300px;
    background:linear-gradient(180deg,rgba(40,22,18,0) 0%,rgba(60,40,34,.35) 40%,rgba(235,232,228,.6) 100%)}
  .slide-title{position:absolute;left:146px;top:230px;height:60px;background:var(--panel);border-radius:3px;
    color:#fff;font-size:26px;font-weight:700;padding:0 32px 0 17px;line-height:60px;white-space:nowrap}
  .slide-text{position:absolute;left:146px;top:297px;width:378px;height:95px;background:var(--panel-light);border-radius:3px;
    color:#fff;font-family:"Open Sans",sans-serif;font-size:12.5px;line-height:20.5px;padding:15px 17px}
  .slide-arrow{position:absolute;top:267px;width:40px;height:40px;border-radius:50%;background:rgba(90,90,95,.75);
    display:flex;align-items:center;justify-content:center}
  .slide-arrow.prev{left:38px}
  .slide-arrow.next{left:1119px}

  .booking-bar{position:absolute;left:0;top:681px;width:1200px;height:83px;background:var(--cream)}
  .booking-title{position:absolute;left:109px;top:27px;font-size:22px;font-weight:400;color:var(--brown-dark);white-space:nowrap}
  .booking-field{position:absolute;top:22px;width:183px;height:42px;border:1px solid var(--field-border);background:#fbf4e3;
    font-family:"Open Sans",sans-serif;font-size:13px;color:#7a6a58;padding:12px 12px;display:flex;justify-content:space-between;align-items:center}
  .booking-field.arrival{left:325px}
  .booking-field.departure{left:522px}
  .booking-field.adults{left:719px}
  .reserve-btn{position:absolute;left:909px;top:22px;width:182px;height:42px;border-radius:3px;
    background:linear-gradient(180deg,#74411f,#5a2f14);color:#fff;font-size:17px;display:flex;align-items:center;justify-content:center}

  .site-footer{position:absolute;left:0;top:764px;width:1200px;height:62px;background:var(--footer);color:var(--footer-text);font-size:13px}
  .copyright{position:absolute;left:99px;top:23px;white-space:nowrap}
  .social{position:absolute;left:517px;top:15px;display:flex;gap:4px}
  .social span{width:30px;height:30px;border-radius:50%;border:2px solid var(--footer-text);display:block}
  .legal{position:absolute;right:99px;top:23px;text-transform:uppercase;white-space:nowrap}
</style>
</head>
<body>
  <header class="site-header">
    <div class="brand"><span class="brand-square"></span><span class="brand-name">Maple Hall</span></div>
    <nav class="main-nav">
      <a>About Us</a><a>Gallery</a><a>Weddings</a><a>Meetings</a><a>Other Events</a><a>Catering</a><a>Menus</a><a>FAQs</a><a>Testimonials</a><a>Contact</a>
    </nav>
  </header>

  <section class="hero">
    <div class="hero-photo" role="img" aria-label="Dining room with round tables set with white linen, wine glasses and napkins"></div>
    <div class="hero-floor"></div>
    <h1 class="slide-title">WELCOME TO MAPLE HALL</h1>
    <p class="slide-text">Maple Hall is Reno's newest, most elegant special events center. Our onsite staff and catering department can assist you in planning the event you desire.</p>
    <div class="slide-arrow prev"><svg width="14" height="22" viewBox="0 0 14 22"><path d="M11 2 3 11l8 9" fill="none" stroke="#fff" stroke-width="2.5"/></svg></div>
    <div class="slide-arrow next"><svg width="14" height="22" viewBox="0 0 14 22"><path d="M3 2l8 9-8 9" fill="none" stroke="#fff" stroke-width="2.5"/></svg></div>
  </section>

  <section class="booking-bar">
    <h2 class="booking-title">Schedule an Appointment</h2>
    <div class="booking-field arrival">Arrival Date<svg width="12" height="12" viewBox="0 0 12 12"><rect x="1" y="2" width="10" height="9" fill="none" stroke="#8a7a68"/><path d="M1 5h10M4 1v2M8 1v2" stroke="#8a7a68"/></svg></div>
    <div class="booking-field departure">Departure Date<svg width="12" height="12" viewBox="0 0 12 12"><rect x="1" y="2" width="10" height="9" fill="none" stroke="#8a7a68"/><path d="M1 5h10M4 1v2M8 1v2" stroke="#8a7a68"/></svg></div>
    <div class="booking-field adults">Adults<svg width="12" height="12" viewBox="0 0 12 12"><rect x="1" y="2" width="10" height="9" fill="none" stroke="#8a7a68"/><path d="M1 5h10M4 1v2M8 1v2" stroke="#8a7a68"/></svg></div>
    <div class="reserve-btn">RESERVE Online</div>
  </section>

  <footer class="site-footer">
    <p class="copyright">©2013 - 2014 Maple Hall at Pine Ridge, All Rights Reserved.</p>
    <div class="social" aria-label="Social links"><span></span><span></span><span></span><span></span><span></span></div>
    <p class="legal">Privacy Policy / Careers</p>
  </footer>
</body>
</html>
```